KDWB Business Card

Looking for a business card design to incorporate our branding. We want to only use the colors listing in the Branding Package (attached).
Updates

Target Market(s)

People who need their phone or device fixed.

Industry/Entity Type

Electronics

Contact Information for Business Card

Please use:

Brightwick Gadget Clinic LLC
4810 E Harlow Ridge Rd
Suite 417
San Antonio, TX 78163

Marcus Delgrove, Store Manager

(210) 555-0147

Requirements
Must have
• Must include the colors that are contained within the Branding Package PDF file.

```html
<!DOCTYPE html>
<html lang="en">
<head>
<meta charset="utf-8">
<title>Brightwick Gadget Clinic – Business Card</title>
<link rel="stylesheet" href="https://fonts.googleapis.com/css2?family=Arimo:wght@400;700&display=swap">
<style>
  :root {
    --backdrop: #3a3532;
    --card-white: #ffffff;
    --photo-light: #eceef2;
    --photo-mid: #d9dbe0;
    --band-grey: #58595b;
    --brand-orange: #f26522;
    --text-white: #ffffff;
  }
  * { margin: 0; padding: 0; box-sizing: border-box; }
  html, body { width: 1200px; height: 764px; overflow: hidden; }
  body {
    background: var(--backdrop);
    font-family: "Arimo", Arial, sans-serif;
    position: relative;
  }
  .card {
    position: absolute;
    top: 233px;
    width: 520px;
    height: 298px;
    overflow: hidden;
    box-shadow: 0 10px 24px rgba(0,0,0,.45);
  }
  .card--front { left: 50px; background: var(--band-grey); }
  .card--back { left: 630px; background: var(--card-white); }

  .card__photo {
    position: absolute; inset: 0;
    background: linear-gradient(120deg, var(--photo-light) 0%, var(--photo-mid) 50%, var(--photo-light) 100%);
  }
  .card__band { position: absolute; inset: 0; }

  .brand {
    position: absolute;
    display: flex;
    align-items: center;
    gap: 10px;
  }
  .brand__mark {
    width: 34px; height: 34px;
    background: var(--brand-orange);
    border-radius: 6px;
    flex: none;
  }
  .brand__name {
    font-size: 17px;
    font-weight: 400;
    color: var(--brand-orange);
    white-space: nowrap;
  }
  .card--front .brand { left: 38px; top: 84px; }
  .card--back .brand { left: 50%; top: 50%; transform: translate(-50%, -50%); }
  .card--back .brand__mark { width: 44px; height: 44px; border-radius: 8px; }
  .card--back .brand__name { font-size: 28px; }
  .card--back .card__photo { opacity: .55; }

  .person {
    position: absolute;
    left: 40px; bottom: 40px;
  }
  .person__name { font-size: 26px; color: var(--text-white); line-height: 1.1; }
  .person__role { font-size: 13px; color: var(--brand-orange); margin-top: 4px; }

  .contact {
    position: absolute;
    right: 24px; top: 120px;
    text-align: right;
    color: var(--text-white);
    font-size: 12px;
    line-height: 1.45;
  }
  .contact__row { display: flex; justify-content: flex-end; align-items: flex-start; gap: 8px; }
  .contact__icon {
    width: 12px; height: 12px;
    flex: none; margin-top: 2px;
  }
  .contact__address { margin-top: 6px; }
</style>
</head>
<body>

  <section class="card card--front" aria-label="Business card front">
    <div class="card__photo" role="img" aria-label="Faded photo of phones being repaired on a workbench"></div>
    <svg class="card__band" width="520" height="298" viewBox="0 0 520 298" aria-hidden="true">
      <polygon points="0,182 285,182 305,98 520,98 520,298 0,298" fill="var(--band-grey)"/>
    </svg>

    <div class="brand">
      <span class="brand__mark"></span>
      <span class="brand__name">Brightwick Gadget Clinic</span>
    </div>

    <div class="contact">
      <div class="contact__row">
        <span>(210) 555-0147</span>
        <svg class="contact__icon" viewBox="0 0 12 12" aria-hidden="true">
          <rect width="12" height="12" fill="var(--brand-orange)"/>
          <path d="M3.5 2.5h1.5l.8 2-1 .8a5 5 0 0 0 2 2l.8-1 2 .8v1.5a1 1 0 0 1-1 1A6.5 6.5 0 0 1 2.5 3.5a1 1 0 0 1 1-1z" fill="#fff"/>
        </svg>
      </div>
      <div class="contact__row contact__address">
        <span>4810 E Harlow Ridge Rd<br>Suite 417, San Antonio, TX 78163</span>
        <svg class="contact__icon" viewBox="0 0 12 12" aria-hidden="true">
          <rect width="12" height="12" fill="var(--brand-orange)"/>
          <path d="M6 2a2.6 2.6 0 0 1 2.6 2.6C8.6 6.6 6 10 6 10S3.4 6.6 3.4 4.6A2.6 2.6 0 0 1 6 2z" fill="#fff"/>
          <circle cx="6" cy="4.6" r="1" fill="var(--brand-orange)"/>
        </svg>
      </div>
    </div>

    <div class="person">
      <p class="person__name">Marcus Delgrove</p>
      <p class="person__role">Store Manager</p>
    </div>
  </section>

  <section class="card card--back" aria-label="Business card back">
    <div class="card__photo" role="img" aria-label="Very faint photo of hands repairing a phone"></div>
    <div class="brand">
      <span class="brand__mark"></span>
      <span class="brand__name">Brightwick Gadget Clinic</span>
    </div>
  </section>

</body>
</html>
```